Morvel's Cocktail Bar & Cigar Lounge

PLEASE DO NOT START WORKING ON THIS PROJECT BEFORE YOU READ ALL OF THE TEXT!!!
Project Title
Morvel’s Cocktail Bar & Cigar Lounge — Full Website Design (Wix)
Project Overview
We are seeking a designer to create a sophisticated, 1920s-inspired website for Morvel’s Cocktail Bar & Cigar Lounge, located in Kilchberg, Zurichsee, Switzerland. The site will be built on Wix and must include an art deco, luxury look, clear booking functionality, and downloadable menu.

Brand & Visual Direction
Brand: Morvel’s Cocktail Bar & Cigar Lounge
Logo: Logo_morvels_bar_black.jpg
Style: 1920s-inspired, art deco, sophisticated luxury, timeless, exclusive, subtle spectacle
Color Palette: Emerald green, gold, black, cream
Icons/Motifs: Martini glass, cigar, champagne flute, art deco borders, geometric patterns
Typography: Elegant serif for headlines (e.g., Playfair Display, Cormorant Garamond); clean sans-serif for body (e.g., Lato, Open Sans, Montserrat)
Image Style: Moody, warm lighting; classic cocktails; vintage barware; subtle 1920s hints; lounge ambiance; cigars; elegant guests
Sitemap & Main Pages
Home
About
Events
Menu
Gallery
Reservations
Contact
Website Copy
Home
Zurich’s Most Exclusive Cocktail Bar & Cigar Lounge

Timeless sophistication. Intelligent indulgence. A sanctuary by the lake.

[Reserve Your Table] (CTA Button)
A New Era on the Lake

Morvel’s invites you into a world where elegance meets camaraderie, and every visit feels like a privilege. Step through our doors and discover a connoisseur’s sanctuary inspired by the golden age of the 1920s—reimagined for Zurich’s most discerning guests.
Signature Experiences Await
Ladies Night, Every Friday: Two cocktails for the price of one, exclusively for the ladies.
Saturday Event Series: Oyster Night, Pata Negra Night, Champagne & Caviar Night, and Vintage Havana Night—each a celebration of taste and refinement.
Curated Cocktails & Cigars: Savor our expertly crafted cocktails, rare spirits, and a handpicked selection of premium cigars.
Meet Your Hosts

In 2025, a new partnership brings fresh energy to Morvel’s. Hospitality expert Orla Venstrup (Lanternhook Productions) joins forces with renowned bar professional Pavel Ducray (Glass Keeper at Hand) to elevate your experience and set a new standard for luxury in Zurichsee.
Gallery Preview

[Slideshow or mosaic of atmospheric images: cocktails, lounge ambiance, cigars, elegant guests]
Reserve Your Table

Secure your place at Zurich’s most exclusive bar.

Phone: 076 418 63 57

Email: contact@morvels-example.ch

Online: www.morvels-example.ch
Footer:

Uferweg 14, 8802 Kilchberg, Switzerland

Open Tuesday–Saturday, 17:00–00:00 | October–March
About
Our Story

Morvel’s Cocktail Bar & Cigar Lounge was born from a passion for refined hospitality and a love for the timeless rituals of the world’s great bars. Inspired by the golden age of the 1920s, our lounge is a haven for those who appreciate intelligent indulgence, subtle spectacle, and genuine connection.
A New Chapter: Partnership & Vision

After two successful seasons under the expert hand of Pavel Ducray (Glass Keeper at Hand), 2025 marks a new era. Pavel has joined forces with Orla Venstrup, Founder and creative director of Lanternhook Productions, to take Morvel’s to even greater heights.
Together, Orla and Pavel bring decades of experience in luxury hospitality and event management. Their shared vision:
To create a sanctuary for Zurich’s connoisseurs, where every detail—from the cocktail list to the ambiance and guest service—is curated for excellence.
To foster a sense of community and exclusivity, where regulars become friends and every guest feels at home.
Our Philosophy

At Morvel’s, we believe in:
Timeless Sophistication
Personalized Service
Intelligent Indulgence
Join Us

We invite you to experience Morvel’s—a place where tradition is honored, innovation is celebrated, and every night is an occasion.
Events
Signature Events at Morvel’s

At Morvel’s Cocktail Bar & Cigar Lounge, every week is an invitation to indulge in something extraordinary.
Ladies Night – Every Friday

Every Friday, ladies enjoy two cocktails for the price of one.
Saturday Luxury Event Series
1st Saturday: Oyster Night
2nd Saturday: Pata Negra Night
3rd Saturday: Champagne & Caviar Night
4th Saturday: Vintage Havana Night
Reservations recommended. Limited seating for all special events.
Private Events & Corporate Gatherings

Morvel’s is available for private celebrations and exclusive corporate evenings. Contact us to discuss your bespoke event.
Menu
Menu 2025/2026
All prices in Swiss Francs (CHF), incl. 8.1% VAT
Menu Classics
Old Fashioned — 18.00

Mint Julep — 18.00

Bees Knees — 18.00

French 75 — 23.00

Mary Pickford — 18.00

Sidecar — 18.00
Gin Cocktails
Negroni — 18.00

Charly Chaplin — 18.00

Southside — 18.00

Clover Club — 18.00

Aviation — 18.00
Vodka Cocktails
Cosmopolitan — 18.00

Garrison Lane — 18.00

Champ — 18.00

Polly Punch — 18.00

Bloody Mary — 18.00
Rum Cocktails
Rum Buck — 18.00

Rum Raisin — 23.00

Old Cuban — 18.00

Mojito — 18.00

Hillbilly — 18.00
Whiskey Cocktails
Dirty Old Bastard — 18.00

Blood and Sand — 18.00

Smoked Boulevardier — 18.00

Lynchburg Lemonade — 18.00

Manhattan — 18.00
Tequila Drinks
Mezcal Last Word — 18.00

Margarita — 18.00

Beachtwister — 18.00

Mexican Mint Smash — 18.00

The 212 — 18.00
Joker Drinks
Adas Sour — 18.00

Basil Smash — 18.00

Espresso Martini — 18.00

Port & Tonic — 18.00

Shelby Ginger — 18.00

Moscow Mule — 18.00

Tiefseetaucher — 28.00
Mocktails
The Fluffy Rose — 15.00

Lonesome Shelby — 16.00

Amaretto Sour — 16.00

Sober Tommy — 16.00

The Hillbilly Bobs No Ruckus — 16.00
Deals
Churchill Deal — 29.00

Upper Deck Deal — 22.00

Lower Deck Deal — 16.00
Sparkling & Champagne
Poggio del Vento Prosecco — 1 dl 9.50 / 7.5 dl 57.00

Lucien Ferrand Champagne — 1 dl 17.00 / 7.5 dl 105.00

Dumarest-Vallon Champagne — 7.5 dl 153.00
Beer
Uferbueb, Chäche Lump — 2.5 dl 6.00 / 4 dl 8.00

Beer of the Month — Ask the bartender

Kranzhofener Weizenbier — 5 dl 9.50

Malthauser Goldstück — 3 dl 6.50 / 5 dl 9.00

KVRN Plain, Alcohol Free — 3 dl 6.50
Soft Drinks & Coffee
Sparkling & Still Water (5 dl) — 5.50

Fizzo Kola / Zero (3 dl) — 5.50

Tonic / Ginger Ale / Ginger Beer / Bitter Lemon (2 dl) — 5.50

Fruit Juice Spritzer (5 dl) — 7.50

Grove Yerba (3 dl) — 6.50

Rossamaro — 6.00

Velbino — 6.00

Coffee / Espresso — 5.50

Tea & Rum — 8.50

Coffee Schnaps — 8.50
Gallery
A Glimpse Inside Morvel’s

Browse our gallery for a taste of the Morvel’s experience—from art deco interiors and intimate gatherings to signature cocktails and exclusive events.

[Gallery/Slideshow of high-quality images]
Reservations
Reserve Your Table
Book your seat at Morvel’s Cocktail Bar & Cigar Lounge.

Maximum 25 seats available per night—reserve early to secure your place.
Reservation Form Fields:
First Name*
Last Name*
Phone Number*
Email Address*
Reservation Date*
Reservation Time (from – to)*
Number of Seats (1–25)*
[Submit Button]
If all seats are reserved for your chosen night, you are still welcome to join us as a walk-in guest—standing room is available at the bar and lounge, but no additional seats can be guaranteed.
You will receive a confirmation once your reservation is complete. For group bookings or special requests, please contact us directly.
Contact
Contact Morvel’s

Address: Uferweg 14, 8802 Kilchberg, Switzerland

Phone: 076 418 63 57

Email: contact@morvels-example.ch

Website: www.morvels-example.ch

Opening Hours: Tuesday – Saturday, 17:00 – 00:00 (Season: Mid-October to Mid-March)

Follow Us: Instagram | Facebook | LinkedIn | X (Twitter)

Getting Here: Conveniently located by the lake in Kilchberg. Parking is available.
Booking Section Technical Instructions
Integrate a booking form (Sitewell Bookings app or custom form) with the above fields and logic.
Enforce a hard cap of 25 reserved seats per night.
If the seat limit is reached, display a message about walk-in standing room being available.
Ensure the form is mobile-friendly and art deco styled.
Send all bookings to admin email (contact@morvels-example.ch) and store in Sitewell dashboard.
Notify admin when a night is fully booked for seats.
Add reCAPTCHA or spam protection.
Additional Instructions for Designer
Platform: Build on Sitewell.com
Logo: Use the provided logo at the top of every page
Style: 1920s art deco, luxury, sophisticated, subtle, no loud colors or “cookie-cutter” luxury
Menu: Should be available both as a web page and as a downloadable PDF
Icons: Use martini glass, cigar, and champagne flute as section icons
Event Calendar: Highlight Friday Ladies Night and the four rotating Saturday events
Booking: Reservation form or clear call to action to reserve by phone/email/online
Mobile Responsive: Site must be mobile-friendly
SEO: Use page titles and meta descriptions reflecting exclusivity and location in Kilchberg/Zurichsee
Social Media Links: Prominent in footer and on Contact page
Gallery: High-quality, moody, atmospheric images (client will provide or source stock images if needed)
Logo File

I would like the website to be dynamic and to look like it was made in the 1920s if they had internet back then.

End of Brief

Target Market(s)

Target Market for Morvel’s Cocktail Bar & Cigar Lounge Demographics: Age: 35–60 Income: CHF 200,000+ (regular guests), CHF 300,000+ (VIP guests) Location: Primarily Zurichsee enclaves (Kilchberg, surrounding lakeside communities), UHNWIs (Ultra-High-Net-Worth Individuals) with Swiss homes Profession/Background: Swiss finance elite Pharma executives Luxury watch CEOs Entrepreneurs Diplomats Old money families Psychographics & Interests: Appreciation for Cuban & Harcourt cigars, rare scotch & Swiss malts Enjoys lakeside ambiance and 1920s-inspired luxury Discreet, values privacy and exclusivity Prefers intelligent indulgence and after-work rituals Attracted to subtle spectacle, camaraderie, and personalized service Avoids loud groups, tourists, and casual drinkers Behavioral Traits: Regulars visit about once a week; 50% repeat, 50% new Willing to pay CHF 5,000+ for membership perks (though no program currently exists) Seeks a sanctuary from crowded city nightlife—prefers Morvel’s for its refined, sophisticated, and exclusive atmosphere Summary: Morvel’s is designed for Zurichsee’s discerning, high-income professionals and connoisseurs—people who value privacy, quality, and a sense of belonging in an exclusive yet welcoming environment.

Industry/Entity Type

Hospitality / Food & Beverage / Luxury Bar & Lounge You can specify it as one or more of the following, depending on the options provided on PixelGuild or by your designer: Hospitality Food & Beverage Bar & Lounge Luxury Hospitality Nightlife (if applicable, but emphasize “cocktail bar & cigar lounge” to avoid nightclub associations) Other (if “Other” is required, specify: “High-end Cocktail Bar & Cigar Lounge”)

Coding

Number of Pages Required

Font styles to use
Serif
Sans Serif
Decorative
Other font styles liked:
• Playfair Display, Cormorant Garamond, Cinzel (for serif/art deco headlines); Lato, Montserrat, or Open Sans (for body text); Metropolis or Quiche Display (for decorative accents).

Colors

Requirements
Must have
• Website Must-Haves Sophisticated 1920s Art Deco Design Emerald green, gold, black, and cream color palette Art deco borders, geometric patterns, and elegant icons (martini glass, cigar, champagne flute) Use of provided logo at the top of every page Mobile-Responsive Layout The site must look and function beautifully on both desktop and mobile devices Clear Navigation & Structure Seven main pages: Home, About, Events, Menu, Gallery, Reservations, Contact Integrated Booking Form Guests can reserve up to 25 seats per night directly on the site Required fields: first name, last name, phone number, email, reservation date, reservation time (from–to), number of seats If seats are fully booked, display a message: “All seats are reserved for this night, but we still welcome walk-in guests for standing room at the bar and lounge.” Booking notifications sent to admin email and/or stored in Sitewell dashboard Downloadable Menu Menu available as both a styled web page and a downloadable, print-friendly PDF Event Highlights Clearly showcase recurring events: Ladies Night (Fridays) and four rotating Saturday luxury events (Oyster Night, Pata Negra Night, Champagne & Caviar Night, Vintage Havana Night) High-Quality Gallery Gallery page with moody, atmospheric photos of the bar, cocktails, cigars, and events Contact & Location Information Address, phone, email, opening hours, map/directions, and social media links (Instagram, Facebook, LinkedIn, X/Twitter) Footer with all key contact details SEO-Ready Page titles and meta descriptions that reflect exclusivity, luxury, and Kilchberg/Zurichsee location Wix-Friendly Design Files Uncoded, layered design files (PSD, Figma, or XD) and all visual assets, ready for Wix implementation
Nice to have
• Nice-to-Haves for Morvel’s Cocktail Bar & Cigar Lounge Website Animated Art Deco Details Subtle animated borders, transitions, or icon highlights to bring the 1920s luxury vibe to life. Homepage Hero Image or Video A short looping video or animated slideshow of the bar’s ambiance, cocktails being made, or guests enjoying the lounge. Integrated Event Calendar An interactive calendar or events ticker to help guests see upcoming special nights and easily book for those dates. Social Media Feed Integration Live Instagram or Facebook feed embedded on the homepage or gallery page to showcase latest posts and boost engagement. Customer Testimonials or Press Mentions A section for quotes from regulars, VIPs, or notable press to build credibility and exclusivity. Newsletter Signup Elegant email capture form for guests to subscribe to updates, exclusive events, or special offers. Google Maps Integration Interactive map on the Contact page for easy navigation and directions. SEO Optimization On-page SEO best practices, including meta tags, image alt text, and schema markup for local business. Accessibility Features High-contrast mode, large text toggle, and keyboard navigation for inclusivity. Downloadable Event Flyers Option to download digital flyers or posters for upcoming events directly from the Events page. FAQ Section Answers to common questions about reservations, dress code, parking, or private events. Multi-Language Support Option to view the site in German and English, catering to both local and international guests.
Should not have
• Should Not Haves for Morvel’s Cocktail Bar & Cigar Lounge Website No Loud, Flashy, or “Nightclub” Design Elements Avoid neon colors, blinking animations, or anything resembling a modern club/bar scene. No “cookie-cutter luxury” or generic bar imagery. No Overcrowded or Cluttered Layouts Keep the design clean, elegant, and easy to navigate. Avoid excessive text blocks, too many pop-ups, or busy backgrounds. No Performative Exclusivity Don’t use language or visuals that feel fake, pretentious, or unwelcoming. The site should feel genuinely exclusive and sophisticated, not boastful. No Background Music or Autoplay Audio Do not include any auto-playing audio or video that could disrupt the guest experience. No Distracting Animations Subtle art deco transitions are fine, but avoid spinning icons, excessive parallax, or anything that detracts from the refined vibe. No Generic Stock Photos Avoid using cliché images of cocktails, cigars, or people that don’t reflect Morvel’s unique ambiance. Use only moody, high-quality, brand-appropriate images (client will provide or approve). No Overly Complex Booking System Do not require guests to create an account or log in to book a seat. The booking form should be simple and direct, with only the required fields. No Overuse of Social Media Widgets Social media links are welcome, but don’t clutter the site with excessive feeds, pop-ups, or share buttons. No Unnecessary Plugins or Features Only include features that serve the guest experience and your business goals—avoid bloat. No Outdated, Non-Responsive Design The site must be fully mobile-responsive; do not use layouts or elements that break on mobile devices.

```html
<!DOCTYPE html>
<html lang="en">
<head>
<meta charset="utf-8">
<title>Morvel’s Cocktail Bar &amp; Cigar Lounge — Kilchberg</title>
<link rel="stylesheet" href="https://fonts.googleapis.com/css2?family=Playfair+Display:wght@600;700&family=Lato:wght@400;700&display=swap">
<style>
:root{
  --emerald:#12332e;
  --emerald-dark:#0c2420;
  --gold:#b4875a;
  --tan:#b3875a;
  --cream:#f1e6d0;
  --paper:#d6bb8e;
  --paper-dark:#8a6a43;
  --ink:#140d07;
  --brown-text:#7d6651;
  --white:#ffffff;
}
*{box-sizing:border-box;margin:0;padding:0}
html,body{width:1200px;height:5021px;overflow:hidden}
body{font-family:"Lato",sans-serif;background:var(--cream);color:var(--ink);position:relative}
.abs{position:absolute}
.serif{font-family:"Playfair Display",serif}

/* top bar */
.topbar{left:0;top:0;width:1200px;height:28px;background:var(--emerald-dark);color:var(--cream);font-size:14px;display:flex;justify-content:space-between;align-items:center;padding:0 112px}

/* hero */
.hero{left:0;top:28px;width:1200px;height:657px;background:radial-gradient(ellipse at 68% 55%,#5a3a1c 0%,#2b1c0e 28%,#10140f 60%,#070a08 100%)}
.hero-edge{left:0;top:633px;width:1200px;height:52px;background:linear-gradient(180deg,#6b4a2a,#c9a57a 60%,#e8d6b6)}
.logo{font-family:"Playfair Display",serif;font-weight:600;color:var(--cream)}
.nav{left:392px;top:74px;display:flex;gap:33px;font-size:13px;color:var(--cream)}
.nav .active{color:#d7a56c}
.contact-btn{left:978px;top:66px;width:112px;height:40px;background:var(--emerald);color:var(--cream);font-weight:700;font-size:15px;display:flex;align-items:center;justify-content:center;border-radius:3px}
.hero h1{left:112px;top:203px;font-size:54px;line-height:72px;color:var(--white);font-weight:700}
.hero-sub{left:112px;top:364px;font-size:18px;color:var(--cream)}
.hero-cta{left:112px;top:415px;width:162px;height:44px;background:var(--emerald);color:var(--cream);font-size:14px;font-weight:700;display:flex;align-items:center;justify-content:center;border-radius:3px}
.play{left:295px;top:422px}

/* ribbon heading */
.ribbon{background:var(--emerald);color:var(--cream);font-family:"Playfair Display",serif;font-weight:700;display:flex;align-items:center;justify-content:center;clip-path:polygon(0 0,100% 0,96% 50%,100% 100%,0 100%,4% 50%)}

.intro-text{left:190px;top:845px;width:820px;text-align:center;color:var(--brown-text);font-size:15px;line-height:30px}

/* events */
.events{left:0;top:1005px;width:1200px;height:569px;background:var(--tan)}
.card{width:300px;height:390px;top:1134px;background:linear-gradient(160deg,#b99b6f,#9a7b53);border:3px solid #3a2815;clip-path:polygon(14px 0,calc(100% - 14px) 0,100% 14px,100% calc(100% - 14px),calc(100% - 14px) 100%,14px 100%,0 calc(100% - 14px),0 14px);padding:12px;color:var(--white);text-align:center}
.card .photo{width:100%;height:214px;border-radius:2px}
.card h3{font-size:16px;font-weight:700;margin-top:24px}
.card p{font-size:12px;line-height:21px;margin:10px 18px 0;color:#f7ecda}

/* hosts */
.hosts-text{left:105px;top:1797px;width:452px;font-size:12.5px;line-height:25px;text-align:justify;color:#3a2c20}
.hosts-photo{left:643px;top:1660px;width:442px;height:286px;background:radial-gradient(ellipse at 50% 40%,#8a5a2a,#4a2a16 45%,#1f1a14 80%)}

/* testimonials */
.testi{left:0;top:2036px;width:1200px;height:493px;background:var(--ink)}
.tcard{top:2221px;width:473px;height:234px;border:2px solid var(--paper-dark);padding:10px}
.tcard .inner{width:100%;height:100%;background:linear-gradient(160deg,#d8bf92,#c2a474);position:relative;padding:24px 26px}
.avatar{width:64px;height:64px;border-radius:50%;background:radial-gradient(circle,#8b7b6a,#3c332b);border:3px solid #efe3cb}
.tname{position:absolute;left:110px;top:48px;font-size:17px;color:#2a1e12}
.quote-mark{position:absolute;right:28px;top:30px;font-family:"Playfair Display",serif;font-size:44px;color:var(--emerald);line-height:1}
.tquote{font-size:13px;line-height:26px;color:#3a2b1c;margin-top:18px;text-align:justify}

/* faq */
.faq-item{left:109px;width:489px;height:50px;background:linear-gradient(180deg,#dcc69c,#c6aa7b);border:2px solid #8a6f4c;border-radius:4px;display:flex;align-items:center;justify-content:space-between;padding:0 20px;font-size:13px;color:#2a1e12}
.faq-item.open{background:var(--emerald);color:var(--cream);border-color:#071814}
.faq-answer{left:647px;top:2723px;width:440px;height:316px;background:linear-gradient(160deg,#dcc59a,#c8ac7d);border:2px solid #9b7f58;padding:30px 36px}
.faq-answer h3{font-size:23px;font-weight:400;font-family:"Lato",sans-serif;color:#22170e}
.faq-answer p{font-size:15px;line-height:29px;color:#3a2b1c;margin-top:18px}

/* reserve */
.reserve{left:0;top:3127px;width:1200px;height:500px;background:var(--ink)}
.reserve-photo{left:620px;top:3127px;width:580px;height:500px;background:radial-gradient(ellipse at 70% 20%,#8a5a22,#3a2412 35%,#180f08 75%)}
.reserve-sub{left:121px;top:3312px;font-size:18px;color:var(--cream)}
.crow{left:112px;display:flex;align-items:center;gap:57px;color:var(--white);font-size:28px}
.cicon{width:40px;height:40px;border-radius:50%;background:var(--white);display:flex;align-items:center;justify-content:center}

/* gallery */
.gphoto{top:3837px;height:328px;clip-path:polygon(34px 0,calc(100% - 34px) 0,100% 34px,100% calc(100% - 34px),calc(100% - 34px) 100%,34px 100%,0 calc(100% - 34px),0 34px)}
.arrow{width:28px;height:28px;border-radius:50%;display:flex;align-items:center;justify-content:center}

/* newsletter */
.news{left:111px;top:4272px;width:976px;height:368px;background:radial-gradient(ellipse at 50% 40%,#3a2412,#1a1008 70%)}
.news-text{left:340px;top:4410px;width:520px;text-align:center;color:var(--cream);font-size:12.5px;line-height:25px}
.news-input{left:282px;top:4525px;width:507px;height:47px;background:var(--white);border-radius:4px;font-size:12px;color:#333;display:flex;align-items:center;padding-left:10px}
.news-btn{left:797px;top:4525px;width:111px;height:47px;background:var(--emerald);color:var(--cream);font-size:15px;font-weight:700;display:flex;align-items:center;justify-content:center;border-radius:3px}

/* footer */
.footer{left:0;top:4724px;width:1200px;height:297px;background:var(--ink)}
.frow{display:flex;align-items:center;gap:14px;color:var(--cream);font-size:14px}
.social{width:29px;height:29px;border-radius:50%;background:var(--white)}
.social.emerald{background:#0f6d63}
.frule{left:111px;top:4983px;width:976px;height:2px;background:#cfc3ad}
.copy{left:0;top:4995px;width:1200px;text-align:center;color:var(--cream);font-size:13px}
</style>
</head>
<body>

<div class="abs topbar"><span>Ladies Night – Every Friday</span><span>Saturday Luxury Event Series</span><span>Signature Events at Morvel’s</span></div>

<section class="abs hero" role="img" aria-label="Dim lounge with a whisky tumbler, a champagne flute and a cigar resting on a tray"></section>
<div class="abs hero-edge"></div>
<div class="abs logo" style="left:112px;top:52px;font-size:48px">Morvel’s</div>
<nav class="abs nav"><span class="active">Home</span><span>About</span><span>Events</span><span>Menu</span><span>Gallery</span><span>Reservations</span><span>⊕ ENG ⌄</span></nav>
<div class="abs contact-btn">CONTACT</div>
<h1 class="abs serif hero">Zurich’s Most Exclusive<br>Cocktail Bar &amp; Cigar</h1>
<h1 class="abs serif" style="left:112px;top:203px;font-size:54px;line-height:72px;color:#fff;font-weight:700">Zurich’s Most Exclusive<br>Cocktail Bar &amp; Cigar</h1>
<p class="abs hero-sub">Timeless sophistication. Intelligent indulgence. A sanctuary by the lake.</p>
<div class="abs hero-cta">Reserve Your Table</div>
<svg class="abs play" width="32" height="32" viewBox="0 0 32 32"><circle cx="16" cy="16" r="15" fill="#fff"/><circle cx="16" cy="16" r="11" fill="#12332e"/><path d="M13 10l9 6-9 6z" fill="#fff"/></svg>

<h2 class="abs ribbon" style="left:340px;top:772px;width:508px;height:58px;font-size:40px">A New Era on the Lake</h2>
<p class="abs intro-text">Morvel’s invites you into a world where elegance meets camaraderie, and every visit feels like a privilege. Step through our doors and discover a connoisseur’s sanctuary inspired by the golden age of the 1920s—reimagined for Zurich’s most discerning guests.</p>

<section class="abs events"></section>
<h2 class="abs ribbon" style="left:448px;top:1041px;width:310px;height:58px;font-size:40px">Our Events</h2>
<article class="abs card" style="left:129px"><div class="photo" role="img" aria-label="Two whisky tumblers with ice" style="background:radial-gradient(circle at 45% 55%,#c9772a,#5a2c0e 60%,#1a0d05)"></div><h3>Ladies Night, Every Friday</h3><p>Two cocktails for the price of one, exclusively for the ladies.</p></article>
<article class="abs card" style="left:458px"><div class="photo" role="img" aria-label="Vintage red car before a lit grand hotel at night" style="background:linear-gradient(180deg,#2a2318,#7a5424 50%,#4a1a12)"></div><h3>Saturday Event Series</h3><p>Oyster Night, Pata Negra Night, Champagne &amp; Caviar Night, and Vintage Havana Night—each a celebration of taste and refinement.</p></article>
<article class="abs card" style="left:785px"><div class="photo" role="img" aria-label="Decanter of spirit with crystal glasses and cigars" style="background:radial-gradient(circle at 40% 60%,#b8702a,#3a2416 55%,#121212)"></div><h3 style="margin-top:28px">Curated Cocktails &amp; Cigars</h3><p>Savor our expertly crafted cocktails, rare spirits, and a handpicked selection of premium cigars.</p></article>

<h2 class="abs ribbon" style="left:111px;top:1700px;width:434px;height:58px;font-size:40px">Meet Your Hosts</h2>
<p class="abs hosts-text">In 2025, a new partnership brings fresh energy to Morvel’s. Hospitality expert Orla Venstrup (Lanternhook Productions) joins forces with renowned bar professional Pavel Ducray (Glass Keeper at Hand) to elevate your experience and set a new standard for luxury in Zurichsee.</p>
<div class="abs hosts-photo" role="img" aria-label="Art deco bar with arched back wall and red leather seating"></div>

<section class="abs testi"></section>
<h2 class="abs ribbon" style="left:333px;top:2102px;width:477px;height:58px;font-size:40px">Client Testimonials</h2>
<article class="abs tcard" style="left:115px"><div class="inner"><div class="avatar"></div><span class="tname">Anselm K., Zürich</span><span class="quote-mark">”</span><p class="tquote">“A hidden gem on the Zurichsee. The cocktails are crafted with perfection — and the cigar selection is unmatched. I’ve never experienced anything like it.”</p></div></article>
<article class="abs tcard" style="left:612px"><div class="inner"><div class="avatar"></div><span class="tname">Livia T., Geneva</span><span class="quote-mark">”</span><p class="tquote">“Stepping into Morvel’s feels like stepping back into the golden age of cocktails. Elegant, intimate, and truly unforgettable.”</p></div></article>

<h2 class="abs ribbon" style="left:327px;top:2618px;width:612px;height:58px;font-size:40px">Frequently Asked Question</h2>
<div class="abs faq-item" style="top:2723px"><span>1.Do I need to make a reservation?</span><span>⌄</span></div>
<div class="abs faq-item" style="top:2790px"><span>2.Can I book the entire lounge for a private event?</span><span>⌄</span></div>
<div class="abs faq-item open" style="top:2856px"><span>3.Do you have a dress code?</span><span>⌃</span></div>
<div class="abs faq-item" style="top:2922px"><span>4.Do you serve food?</span><span>⌄</span></div>
<div class="abs faq-item" style="top:2988px"><span>5.Is smoking allowed inside the lounge?</span><span>⌄</span></div>
<div class="abs faq-answer"><h3>3.Do you have a dress code?</h3><p>Yes. Smart casual to elegant attire is encouraged to match the lounge’s atmosphere. No sportswear or caps, please.</p></div>

<section class="abs reserve"></section>
<div class="abs reserve-photo" role="img" aria-label="Dark wood bar with back-lit bottles and a brass chandelier"></div>
<h2 class="abs ribbon" style="left:111px;top:3210px;width:450px;height:58px;font-size:40px">Reserve Your Table</h2>
<p class="abs reserve-sub">Secure your place at Zurich’s most exclusive bar</p>
<div class="abs crow" style="top:3387px"><span class="cicon"><svg width="22" height="22" viewBox="0 0 24 24"><path fill="#140d07" d="M6.6 10.8a15 15 0 006.6 6.6l2.2-2.2c.3-.3.7-.4 1-.2 1.1.4 2.3.6 3.6.6.6 0 1 .4 1 1V20c0 .6-.4 1-1 1A17 17 0 013 4c0-.6.4-1 1-1h3.5c.6 0 1 .4 1 1 0 1.3.2 2.5.6 3.6.1.3 0 .7-.2 1z"/></svg></span><span>076 418 63 57</span></div>
<div class="abs crow" style="top:3455px"><span class="cicon"><svg width="22" height="22" viewBox="0 0 24 24"><rect x="3" y="6" width="18" height="12" rx="1" fill="#140d07"/><path d="M3 7l9 6 9-6" stroke="#fff" stroke-width="1.5" fill="none"/></svg></span><span>contact@morvels-example.ch</span></div>
<div class="abs crow" style="top:3521px"><span class="cicon"><svg width="24" height="24" viewBox="0 0 24 24" fill="none" stroke="#140d07" stroke-width="1.6"><circle cx="12" cy="12" r="9"/><ellipse cx="12" cy="12" rx="4" ry="9"/><path d="M3 12h18M5 7h14M5 17h14"/></svg></span><span>www.morvels-example.ch</span></div>

<h2 class="abs ribbon" style="left:432px;top:3731px;width:332px;height:58px;font-size:40px">Our Gallery</h2>
<div class="abs gphoto" style="left:107px;width:222px;background:radial-gradient(circle at 50% 55%,#d08a32,#6a3510 55%,#1e0f06)" role="img" aria-label="Whisky tumbler with ice"></div>
<div class="abs gphoto" style="left:339px;width:522px;background:radial-gradient(ellipse at 55% 60%,#b06a22,#3e220c 45%,#0d0a07)" role="img" aria-label="Whisky glass and a smoking cigar on a dark table"></div>
<div class="abs gphoto" style="left:869px;width:222px;background:radial-gradient(circle at 50% 40%,#9a5a2a,#3a1c10 55%,#150c07)" role="img" aria-label="Ornate vintage lounge corner with clock and armchairs"></div>
<div class="abs arrow" style="left:27px;top:3979px;background:var(--emerald)"><svg width="12" height="12" viewBox="0 0 12 12"><path d="M8 1L3 6l5 5" stroke="#fff" stroke-width="2" fill="none"/></svg></div>
<div class="abs arrow" style="left:1133px;top:3979px;background:#c9bfb0"><svg width="12" height="12" viewBox="0 0 12 12"><path d="M4 1l5 5-5 5" stroke="#fff" stroke-width="2" fill="none"/></svg></div>

<section class="abs news" role="img" aria-label="Dim bar interior with warm lamps behind the newsletter panel"></section>
<h2 class="abs ribbon" style="left:330px;top:4334px;width:606px;height:58px;font-size:40px">Suscribe To Our Newsletter</h2>
<p class="abs news-text">Welcome to Morvel’s — Zurichsee’s sanctuary of cocktails, cigars, and timeless indulgence. Each month we bring you highlights from the lounge, upcoming events, and exclusive offers reserved for our valued guests.</p>
<div class="abs news-input">Enter Email Adress</div>
<div class="abs news-btn">SUBSCRIBE</div>

<footer class="abs footer"></footer>
<div class="abs logo" style="left:121px;top:4820px;font-size:66px">Morvel’s</div>
<div class="abs frow" style="left:743px;top:4802px"><svg width="34" height="34" viewBox="0 0 34 34"><circle cx="17" cy="17" r="16" fill="#fff"/><path d="M17 8a6 6 0 00-6 6c0 5 6 12 6 12s6-7 6-12a6 6 0 00-6-6z" fill="#140d07"/><circle cx="17" cy="14" r="2.2" fill="#fff"/></svg><span>Uferweg 14, 8802 Kilchberg, Switzerland</span></div>
<div class="abs frow" style="left:808px;top:4842px"><svg width="34" height="34" viewBox="0 0 34 34"><circle cx="17" cy="17" r="16" fill="#fff"/><path d="M17 9v8l6 4" stroke="#140d07" stroke-width="3" fill="none"/></svg><span>Tuesday–Saturday, 17:00–00:00 |</span></div>
<div class="abs" style="left:946px;top:4891px;display:flex;gap:6px"><span class="social emerald"></span><span class="social"></span><span class="social"></span><span class="social"></span></div>
<div class="abs frule"></div>
<p class="abs copy">© 2025 Morvel’s Bar .All rights reserved</p>

</body>
</html>
```